Harborline Auto LLC

Car Dealer Customer Service
Address: 2874 Cresthaven Road, Marlow Springs, OR 97999
web: www.harborlineautoxq.net
email: harborlineautoxq@mailnest.example
Phone: (555) 555-0148
Phone: (555) 555-0173

```html
<!DOCTYPE html>
<html lang="en">
<head>
<meta charset="utf-8">
<title>Harborline Auto – Business Card</title>
<link href="https://fonts.googleapis.com/css2?family=Montserrat:wght@400;500;800&display=swap" rel="stylesheet">
<style>
  :root {
    --blue: #1d84bd;
    --blue-light: #2596cf;
    --blue-dark: #17709f;
    --gold: #edb544;
    --paper: #f7f7f5;
    --white: #ffffff;
    --backdrop: #1c1c1e;
  }
  * { margin: 0; padding: 0; box-sizing: border-box; }
  html, body {
    width: 1200px; height: 963px; overflow: hidden;
    background: var(--backdrop);
    font-family: "Montserrat", sans-serif;
  }
  .sheet {
    width: 1200px; height: 963px;
    display: flex; flex-direction: column; align-items: center; justify-content: center;
    gap: 44px;
  }
  .card {
    width: 700px; height: 400px; position: relative; overflow: hidden;
    box-shadow: 0 10px 30px rgba(0,0,0,.5);
  }
  /* front */
  .card-front { background: var(--paper); }
  .front-brand {
    position: absolute; left: 0; right: 0; top: 0; height: 190px;
    display: flex; align-items: center; justify-content: center; gap: 16px;
  }
  .brand-dot { width: 34px; height: 34px; border-radius: 50%; background: var(--gold); flex: none; }
  .brand-name {
    font-weight: 800; font-size: 40px; letter-spacing: 1px; text-transform: uppercase;
    color: var(--blue); white-space: nowrap;
  }
  .front-band {
    position: absolute; left: 0; right: 0; bottom: 0; height: 210px;
    background: linear-gradient(180deg, var(--blue-light), var(--blue-dark));
    border-top: 6px solid var(--gold);
    display: flex; align-items: center; padding: 0 40px 0 50px;
    color: var(--white);
  }
  .address { flex: 1; font-size: 16px; line-height: 1.6; font-weight: 500; text-align: right; padding-right: 28px; white-space: nowrap; }
  .divider { width: 1px; height: 130px; background: rgba(255,255,255,.8); flex: none; }
  .contacts { flex: 1.45; list-style: none; padding-left: 26px; font-size: 16px; line-height: 1.85; font-weight: 500; }
  .contacts li { display: flex; align-items: center; gap: 10px; white-space: nowrap; }
  .contacts svg { width: 18px; height: 18px; flex: none; }
  /* back */
  .card-back {
    background: linear-gradient(160deg, var(--blue-light), var(--blue-dark));
    display: flex; align-items: center; justify-content: center; gap: 18px;
  }
  .card-back .brand-name { color: var(--white); font-size: 46px; }
</style>
</head>
<body>
<main class="sheet">
  <section class="card card-front" aria-label="Card front">
    <div class="front-brand">
      <span class="brand-dot"></span>
      <span class="brand-name">Harborline Auto</span>
    </div>
    <div class="front-band">
      <p class="address">2874 Cresthaven Road<br>Marlow Springs, OR 97999</p>
      <span class="divider"></span>
      <ul class="contacts">
        <li><svg viewBox="0 0 20 20"><circle cx="10" cy="10" r="10" fill="#fff"/><path d="M7 5.5l2 2-1 1.3c.7 1.4 1.8 2.5 3.2 3.2l1.3-1 2 2-1.3 1.5C9.8 14 6 10.2 5.5 6.8z" fill="#1d84bd"/></svg>(555) 555-0148</li>
        <li><svg viewBox="0 0 20 20"><circle cx="10" cy="10" r="10" fill="#fff"/><path d="M7 5.5l2 2-1 1.3c.7 1.4 1.8 2.5 3.2 3.2l1.3-1 2 2-1.3 1.5C9.8 14 6 10.2 5.5 6.8z" fill="#1d84bd"/></svg>(555) 555-0173</li>
        <li><svg viewBox="0 0 20 20"><circle cx="10" cy="10" r="10" fill="#fff"/><rect x="5" y="6.5" width="10" height="7" fill="none" stroke="#1d84bd" stroke-width="1.4"/><path d="M5 6.5l5 4 5-4" fill="none" stroke="#1d84bd" stroke-width="1.4"/></svg>harborlineautoxq@mailnest.example</li>
        <li><svg viewBox="0 0 20 20"><circle cx="10" cy="10" r="10" fill="#fff"/><circle cx="10" cy="10" r="5.5" fill="none" stroke="#1d84bd" stroke-width="1.3"/><ellipse cx="10" cy="10" rx="2.3" ry="5.5" fill="none" stroke="#1d84bd" stroke-width="1.1"/><path d="M4.5 10h11" stroke="#1d84bd" stroke-width="1.1"/></svg>www.harborlineautoxq.net</li>
      </ul>
    </div>
  </section>
  <section class="card card-back" aria-label="Card back">
    <span class="brand-dot"></span>
    <span class="brand-name">Harborline Auto</span>
  </section>
</main>
</body>
</html>
```